DESIGN OF STATIONERY - TORVALE MED

WE WORK IN THE FIELD OF HEALTH (IMAGING: MRI - CT ETC.).
WE WOULD LIKE TO CREATE THE ENTIRE STATIONERY DESIGN : LETTERHEAD, BUSINESS CARD, CALENDAR, INVOICES, CD HOLDER, ETC.

Target Market(s)

PERSONS UNDERTAKING HEALTH EXAMINATIONS

```html
<!DOCTYPE html>
<html lang="en">
<head>
<meta charset="utf-8">
<title>Torvale Med – Business Card</title>
<link href="https://fonts.googleapis.com/css2?family=Montserrat:wght@600;700&family=Roboto:wght@400&display=swap" rel="stylesheet">
<style>
  :root {
    --stage: #1b1c1f;
    --paper: #f4f5f6;
    --brand-blue: #1f7fc4;
    --brand-teal: #2bb5a8;
    --ink: #555a60;
    --back-top: #2a86d0;
    --back-bottom: #1561b0;
    --back-mark: #7fb2e6;
  }
  * { box-sizing: border-box; margin: 0; padding: 0; }
  html, body { width: 1200px; height: 900px; overflow: hidden; }
  body {
    background: var(--stage);
    display: flex;
    flex-direction: column;
    align-items: center;
    justify-content: center;
    gap: 56px;
    font-family: "Roboto", sans-serif;
  }
  .card {
    width: 580px;
    height: 375px;
    border-radius: 4px;
    position: relative;
    overflow: hidden;
  }
  /* Front */
  .card-front { background: var(--paper); color: var(--ink); }
  .brand {
    position: absolute;
    top: 70px;
    left: 0; right: 0;
    text-align: center;
  }
  .brand-name {
    font-family: "Montserrat", sans-serif;
    font-weight: 700;
    font-size: 46px;
    letter-spacing: 1px;
    color: var(--brand-blue);
    display: inline-flex;
    align-items: center;
    gap: 12px;
  }
  .brand-dot {
    width: 14px; height: 14px;
    border-radius: 50%;
    background: var(--brand-teal);
  }
  .brand-tagline {
    font-family: "Montserrat", sans-serif;
    font-weight: 600;
    font-size: 15px;
    color: var(--brand-teal);
    margin-top: 6px;
    letter-spacing: 0.5px;
  }
  .details {
    position: absolute;
    top: 190px;
    left: 40px; right: 40px;
    display: flex;
    align-items: center;
    gap: 22px;
  }
  .person { text-align: right; flex: 0 0 220px; }
  .person-name {
    font-family: "Montserrat", sans-serif;
    font-weight: 700;
    font-size: 18px;
    color: var(--brand-blue);
    letter-spacing: 0.5px;
  }
  .person-role {
    font-family: "Montserrat", sans-serif;
    font-weight: 600;
    font-size: 15px;
    color: var(--brand-teal);
    margin-top: 2px;
  }
  .divider { width: 2px; height: 84px; background: var(--brand-teal); }
  .contact-list { list-style: none; font-size: 16px; line-height: 28px; }
  .contact-list li { display: flex; align-items: center; gap: 10px; }
  .contact-list svg { width: 16px; height: 16px; flex: none; }
  .address {
    position: absolute;
    bottom: 40px;
    left: 0; right: 0;
    text-align: center;
    font-size: 15px;
  }
  /* Back */
  .card-back {
    background: linear-gradient(160deg, var(--back-top), var(--back-bottom));
    display: flex;
    flex-direction: column;
    align-items: center;
    justify-content: center;
  }
  .back-name {
    font-family: "Montserrat", sans-serif;
    font-weight: 700;
    font-size: 52px;
    letter-spacing: 1px;
    color: var(--back-mark);
  }
  .back-tagline {
    font-family: "Montserrat", sans-serif;
    font-weight: 600;
    font-size: 16px;
    color: var(--back-mark);
    margin-top: 6px;
  }
</style>
</head>
<body>
  <section class="card card-front">
    <div class="brand">
      <div class="brand-name"><span class="brand-dot"></span>TORVALE MED</div>
      <div class="brand-tagline">Health Care Diagnostic</div>
    </div>
    <div class="details">
      <div class="person">
        <div class="person-name">LUKAS R. VENNER</div>
        <div class="person-role">President</div>
      </div>
      <div class="divider"></div>
      <ul class="contact-list">
        <li>
          <svg viewBox="0 0 16 16" aria-hidden="true"><path fill="#1f7fc4" d="M3.5 1.5l2.5 0 1 3.5-1.6 1.2a8 8 0 0 0 4.4 4.4L11 9l3.5 1v2.5c0 1-1 2-2 2A11 11 0 0 1 1.5 3.5c0-1 1-2 2-2z"/></svg>
          07700 900 318
        </li>
        <li>
          <svg viewBox="0 0 16 16" aria-hidden="true"><rect x="1" y="3" width="14" height="10" rx="1" fill="#1f7fc4"/><path d="M1.5 3.5L8 9l6.5-5.5" stroke="#f4f5f6" stroke-width="1.4" fill="none"/></svg>
          info@torvalemed.com
        </li>
        <li>
          <svg viewBox="0 0 16 16" aria-hidden="true"><circle cx="8" cy="8" r="7" fill="#1f7fc4"/><path d="M1 8h14M8 1c-3 3.5-3 10.5 0 14M8 1c3 3.5 3 10.5 0 14" stroke="#f4f5f6" stroke-width="1" fill="none"/></svg>
          www.torvalemed.com
        </li>
      </ul>
    </div>
    <p class="address">Torvale-Med-R 2nd Floor 18 Kelmarsh Place Glasgow G3 7QD</p>
  </section>

  <section class="card card-back">
    <div class="back-name">TORVALE MED</div>
    <div class="back-tagline">Health Care Diagnostic</div>
  </section>
</body>
</html>
```